Varnex Consulting Business card design.

See our website www.varnexconsulting.example which will give you a good idea of what we are about. The font is called 'Play'.

I'd like a standout business card in keeping with the themes and branding on the website

Target Market(s)

professionals. HR directors

Industry/Entity Type

Business

Contact Information for Business Card

Varnex Consulting PO Box 3172 Merrowdale NSW 2291 1300 485 193 Gavin Threlkeld Principal email: career@varnexconsulting.example ABN: 71203948865

Font styles to use
Other font styles liked:
• Play

Requirements
Must have
• Must have same design colours and branding as website.
• On back I'd prefer a list of the things we do which appears below the name at the header on the website

```html
<!DOCTYPE html>
<html lang="en">
<head>
<meta charset="utf-8">
<title>Varnex Consulting – Business Card</title>
<link rel="stylesheet" href="https://fonts.googleapis.com/css2?family=Play:wght@400;700&display=swap">
<style>
  :root {
    --navy: #0c1f31;
    --blue: #3a8fd0;
    --white: #ffffff;
    --backdrop: #ebe8e3;
    --snow: #2f6fb8;
    --track: #7a4a4a;
    --sea: #5f7f80;
  }
  * { margin: 0; padding: 0; box-sizing: border-box; }
  html, body {
    width: 1189px; height: 1200px; overflow: hidden;
    background: var(--backdrop);
    font-family: "Play", sans-serif;
  }
  .card {
    position: absolute; left: 171px; width: 856px; height: 487px;
    background: var(--navy); overflow: hidden;
    box-shadow: 0 6px 14px rgba(0,0,0,.25);
  }
  .card--front { top: 68px; }
  .card--back  { top: 627px; }
  .abs { position: absolute; line-height: 1; white-space: nowrap; }

  /* front */
  .brand-line { left: 39px; font-size: 61px; font-weight: 700; letter-spacing: 1px; }
  .brand-line--top { top: 39px; color: var(--white); }
  .brand-line--bottom { top: 106px; color: var(--blue); }
  .person-name { top: 47px; right: 37px; font-size: 34px; font-weight: 700; color: var(--white); letter-spacing: .5px; }
  .person-role { top: 78px; right: 37px; font-size: 23px; color: var(--blue); }
  .phone { top: 131px; right: 74px; font-size: 24px; color: var(--white); }
  .phone-icon { top: 129px; right: 37px; width: 27px; height: 25px; }
  .rule { position: absolute; left: 0; width: 100%; }
  .rule--white-top { top: 181px; height: 11px; background: var(--white); }
  .photo-strip { position: absolute; top: 196px; left: 0; width: 100%; height: 204px; background: var(--white); }
  .photo { position: absolute; top: 0; height: 204px; }
  .photo--snow { left: 0; width: 282px; background: linear-gradient(170deg, #1b57a8 0%, var(--snow) 55%, #dfe9f5 100%); }
  .photo--track { left: 289px; width: 281px; background: linear-gradient(180deg, #3c3a4a 0%, #9c7a78 45%, var(--track) 100%); }
  .photo--surf { left: 576px; width: 280px; background: linear-gradient(180deg, #8d9aa0 0%, var(--sea) 55%, #c9d2d3 100%); }
  .rule--white-bottom { top: 404px; height: 5px; background: var(--white); }
  .contact-band { position: absolute; top: 421px; left: 0; width: 100%; height: 66px; background: var(--blue); }
  .contact-icon { position: absolute; top: 21px; width: 27px; height: 25px; }
  .contact-text { top: 22px; font-size: 21px; color: var(--white); }

  /* back */
  .back-title { top: 62px; left: 0; width: 100%; text-align: center; font-size: 61px; font-weight: 700; color: var(--white); letter-spacing: 1px; }
  .back-title span { color: var(--blue); }
  .services-heading { top: 163px; left: 0; width: 100%; text-align: center; font-size: 27px; font-weight: 700; color: var(--blue); }
  .services { position: absolute; top: 200px; left: 0; width: 100%; text-align: center; font-size: 24px; line-height: 34px; color: var(--white); }
  .testimonial { position: absolute; top: 327px; left: 0; width: 100%; text-align: center; font-size: 23px; line-height: 34px; font-style: italic; color: var(--white); }
  .address-band { position: absolute; top: 417px; left: 0; width: 100%; height: 70px; background: var(--white); border-top: 6px solid var(--blue); }
  .address { top: 24px; left: 0; width: 100%; text-align: center; font-size: 22px; font-weight: 700; color: var(--navy); letter-spacing: .5px; }
</style>
</head>
<body>

<section class="card card--front">
  <div class="abs brand-line brand-line--top">VARNEX</div>
  <div class="abs brand-line brand-line--bottom">CONSULTING</div>

  <div class="abs person-name">Employee Name</div>
  <div class="abs person-role">Managing Director</div>
  <div class="abs phone">1300 485 193</div>
  <svg class="abs phone-icon" viewBox="0 0 27 25" aria-hidden="true">
    <rect width="27" height="25" fill="var(--blue)"/>
    <path d="M9 5 l3 0 l1 5 l-2 1.5 q1.5 3.5 4 5 l1.5 -2 l5 1 l0 3 q-1 2 -3 2 q-9 -1 -11 -12 q0 -2.5 1.5 -3.5z" fill="var(--white)"/>
  </svg>

  <div class="rule rule--white-top"></div>
  <div class="photo-strip">
    <div class="photo photo--snow" role="img" aria-label="Photo of a snowboarder jumping over a snowy mountain peak"></div>
    <div class="photo photo--track" role="img" aria-label="Photo of sprinters' hands on the start line of a running track"></div>
    <div class="photo photo--surf" role="img" aria-label="Photo of a surfer riding a breaking wave"></div>
  </div>
  <div class="rule rule--white-bottom"></div>

  <div class="contact-band">
    <svg class="contact-icon" style="left:37px" viewBox="0 0 27 25" aria-hidden="true">
      <rect x="1" y="2" width="25" height="21" fill="var(--white)"/>
      <rect x="4" y="6" width="19" height="13" fill="none" stroke="var(--blue)" stroke-width="1.5"/>
      <path d="M4 6 l9.5 7 l9.5 -7 M4 19 l7 -6 M23 19 l-7 -6" fill="none" stroke="var(--blue)" stroke-width="1.5"/>
    </svg>
    <div class="abs contact-text" style="left:72px">career@varnexconsulting.example</div>

    <svg class="contact-icon" style="left:457px" viewBox="0 0 27 25" aria-hidden="true">
      <rect x="1" y="1" width="25" height="23" fill="var(--white)"/>
      <g fill="none" stroke="var(--blue)" stroke-width="1.3">
        <circle cx="13.5" cy="12.5" r="8"/>
        <ellipse cx="13.5" cy="12.5" rx="3.5" ry="8"/>
        <path d="M5.5 12.5 h16 M7 8 h13 M7 17 h13"/>
      </g>
    </svg>
    <div class="abs contact-text" style="left:499px">www.varnexconsulting.example</div>
  </div>
</section>

<section class="card card--back">
  <div class="abs back-title">VARNEX <span>CONSULTING</span></div>
  <div class="abs services-heading">WE DO</div>
  <div class="services">
    <p>Search &amp; Selection | Career Coaching | Talent Assessment</p>
    <p>Resume Enhancement | Interview Coaching | Leadership Development</p>
    <p>Personal Development Plans | Outplacement</p>
  </div>
  <div class="testimonial">
    <p>“I really loved working with Varnex.</p>
    <p>They really understood my needs and my plans for my professional future.”</p>
  </div>
  <div class="address-band">
    <div class="abs address">PO Box 3172 Merrowdale NSW 2291</div>
  </div>
</section>

</body>
</html>
```